Business Card Design for Flood Rescue 360 - Property Restoration Professionals

I need a business card designed for Flood Rescue 360. We are a full-service property restoration solution. Providing water, fire, smoke & storm restoration as well as mold remediation and full remodel or reconstruction to homes and businesses across Dallas-Fort Worth, TX.
Target Market(s)
home and business owners with insurance covered property damage from water, fire or storm related damage
Industry/Entity Type
property restoration
Contact Information for Business Card
Marcus Pelley General Manager Cell: 214-555-0193 Office: 469-555-0148 email: Marcus@FloodRescue360.example services: Water, Fire, Mold, Reconstruction Tagline: Fast Help When the Water Rises!
Look and feel
Each slider illustrates characteristics of the customer's brand and the style your logo design should communicate.

```html
<!DOCTYPE html>
<html lang="en">
<head>
<meta charset="utf-8">
<title>Flood Rescue 360 – Business Card</title>
<link rel="stylesheet" href="https://fonts.googleapis.com/css2?family=Roboto:wght@900&family=Montserrat:wght@400;700&display=swap">
<style>
  :root {
    --stage: #1c1c1c;
    --card-light: #f4f4f4;
    --card-dark: #252525;
    --brand-blue: #15ade0;
    --ink: #2a2a2a;
    --soft-blue: #e3f3fa;
    --muted-white: #ececec;
  }
  * { box-sizing: border-box; margin: 0; padding: 0; }
  html, body { width: 1200px; height: 1059px; overflow: hidden; background: var(--stage); }
  .stage { position: relative; width: 1200px; height: 1059px; }
  .card { position: absolute; border-radius: 20px; overflow: hidden; }
  .card-front { left: 257px; top: 89px; width: 687px; height: 390px; background: var(--card-light); }
  .card-back { left: 254px; top: 547px; width: 693px; height: 393px; background: var(--card-dark); }

  .wordmark {
    font-family: "Roboto", sans-serif; font-weight: 900; color: var(--brand-blue);
    text-transform: uppercase; line-height: 0.92; letter-spacing: -0.5px;
  }
  .card-front .wordmark { position: absolute; left: 34px; top: 38px; font-size: 50px; }
  .brand-circle { position: absolute; left: 318px; top: 22px; width: 326px; height: 326px; border-radius: 50%; background: var(--soft-blue); }

  .name-tab { position: absolute; left: 0; top: 186px; width: 19px; height: 42px; background: var(--brand-blue); border-radius: 0 5px 5px 0; }
  .person-name { position: absolute; left: 34px; top: 183px; font-family: "Montserrat", sans-serif; font-weight: 700; font-size: 25px; color: var(--brand-blue); letter-spacing: 1px; }
  .person-title { position: absolute; left: 34px; top: 211px; font-family: "Montserrat", sans-serif; font-weight: 400; font-size: 16px; color: var(--ink); letter-spacing: 0.5px; }

  .contact-list { position: absolute; left: 33px; top: 250px; list-style: none; font-family: "Montserrat", sans-serif; font-weight: 400; font-size: 17.5px; color: var(--ink); letter-spacing: 0.4px; }
  .contact-list li { display: flex; align-items: center; height: 27.8px; }
  .contact-list svg { width: 13px; height: 13px; margin-right: 7px; fill: var(--brand-blue); flex: none; }

  .back-brand { position: absolute; left: 0; width: 100%; top: 104px; display: flex; justify-content: center; align-items: center; gap: 14px; }
  .card-back .wordmark { font-size: 56px; }
  .back-circle { width: 120px; height: 120px; border-radius: 50%; background: var(--brand-blue); flex: none; }
  .services, .tagline { position: absolute; left: 0; width: 100%; text-align: center; font-family: "Montserrat", sans-serif; font-weight: 400; font-size: 17.5px; color: var(--muted-white); letter-spacing: 0.6px; }
  .services { top: 316px; }
  .tagline { top: 345px; }
  .services .dot { color: var(--brand-blue); margin: 0 6px; }
</style>
</head>
<body>
<main class="stage">
  <section class="card card-front">
    <div class="brand-circle" aria-hidden="true"></div>
    <h1 class="wordmark">Flood<br>Rescue 360</h1>
    <span class="name-tab" aria-hidden="true"></span>
    <p class="person-name">MARCUS PELLEY</p>
    <p class="person-title">General Manager</p>
    <ul class="contact-list">
      <li><svg viewBox="0 0 16 16"><path d="M2 6c0-2 3-3 6-3s6 1 6 3v1h-3V5.5H5V7H2zM4 8h8l1 6H3z"/></svg>469-555-0148</li>
      <li><svg viewBox="0 0 16 16"><path d="M4 1h8v14H4zM5.5 2.5v9h5v-9z"/></svg>214-555-0193</li>
      <li><svg viewBox="0 0 16 16"><path d="M1 6l7-4 7 4v8H1zM2.5 6.5L8 10l5.5-3.5L8 3.5z"/></svg>Marcus@FloodRescue360.example</li>
      <li><svg viewBox="0 0 16 16"><circle cx="8" cy="8" r="7"/></svg>www.FloodRescue360.example</li>
    </ul>
  </section>

  <section class="card card-back">
    <div class="back-brand">
      <h2 class="wordmark">Flood<br>Rescue 360</h2>
      <span class="back-circle" aria-hidden="true"></span>
    </div>
    <p class="services">Water<span class="dot">•</span>Fire<span class="dot">•</span>Mold<span class="dot">•</span>Reconstruction</p>
    <p class="tagline">Fast Help When the Water Rises!</p>
  </section>
</main>
</body>
</html>
```